Clean Vexlo Ads Banner Design For A Finance Company

Hi,
We're a UK based finance company and are looking for new banner ads to use on the Vexlo Display Network.
We want the end product to stand out by using strong, minimal design - ideally starting from a dark theme, although I'm open to ideas.
The copy should read:
'Fast Bridging Loans From 0.39% PM'
Once we have these designs agreed, we are looking to replicate them for other products, changing only the text on each ad - for example, 'commercial mortgage service you can rely on' or 'development finance service you can rely on'.
The colours used on our website are the following:
Black - #040303
Orange - #f79124
White - #ffffff
Grey - #ffffff
Example ads that I like - https://www.plimrake.com/wp-content/uploads/2021/07/vexlo-display-ads-example-2-final.png.webp
2 - https://qarnelvistahub.com/wp-content/uploads/2020/03/fbdd56ba3bd16c7a8debb13a411de786.jpg

```html
<!DOCTYPE html>
<html lang="en">
<head>
<meta charset="utf-8">
<title>Halvern Finance Limited – Display Banners</title>
<link href="https://fonts.googleapis.com/css2?family=Montserrat:wght@600;700;800&family=Roboto:wght@700&display=swap" rel="stylesheet">
<style>
  :root {
    --canvas-grey: #b3b3b3;
    --label-ink: #1f1f1f;
    --banner-black: #111111;
    --brand-orange: #f79124;
    --white: #ffffff;
    --photo-blue-dark: #1f3050;
    --photo-blue-light: #8fa6bf;
    --photo-warm-dark: #6a574a;
    --photo-warm-light: #d8cbbd;
    --photo-slate-dark: #1c1c1c;
    --photo-slate-light: #5a554f;
  }
  * { margin: 0; padding: 0; box-sizing: border-box; }
  html, body {
    width: 1200px;
    height: 1104px;
    overflow: hidden;
    background: var(--canvas-grey);
  }
  .stage {
    position: absolute;
    left: 0;
    top: 0;
    width: 826px;
    height: 760px;
    transform: scale(1.45278);
    transform-origin: 0 0;
  }
  .size-label {
    position: absolute;
    width: 160px;
    margin-left: -80px;
    text-align: center;
    font-family: "Roboto", Arial, sans-serif;
    font-weight: 700;
    font-size: 20px;
    line-height: 24px;
    color: var(--label-ink);
  }
  .banner {
    position: absolute;
    background: var(--banner-black);
    overflow: hidden;
    box-shadow: 0 3px 10px rgba(0,0,0,0.35);
    text-align: center;
  }
  .banner--336x280 { left: 70px; top: 101px; width: 336px; height: 280px; }
  .banner--300x250 { left: 88px; top: 451px; width: 300px; height: 250px; }
  .banner--300x600 { left: 457px; top: 101px; width: 300px; height: 600px; }

  .brand-name {
    position: absolute;
    left: 0; right: 0;
    font-family: "Montserrat", Arial, sans-serif;
    font-weight: 800;
    color: var(--brand-orange);
    letter-spacing: -0.5px;
  }
  .headline {
    position: absolute;
    left: 0; right: 0;
    font-family: "Montserrat", Arial, sans-serif;
    font-weight: 700;
    color: var(--white);
    letter-spacing: 0.3px;
    white-space: nowrap;
  }
  .headline span { display: block; }
  .divider {
    position: absolute;
    left: 50%;
    width: 44px;
    margin-left: -22px;
    height: 1px;
    background: linear-gradient(90deg, rgba(255,255,255,0), var(--white) 35%, var(--white) 65%, rgba(255,255,255,0));
  }
  .cta {
    position: absolute;
    left: 50%;
    width: 80px;
    margin-left: -40px;
    height: 25px;
    border-radius: 13px;
    background: var(--brand-orange);
    color: var(--white);
    font-family: "Montserrat", Arial, sans-serif;
    font-weight: 700;
    font-size: 7.5px;
    line-height: 25px;
    letter-spacing: 0.2px;
    text-decoration: none;
  }
  .roof {
    position: absolute;
    left: 0;
    bottom: 0;
    width: 100%;
  }

  .banner--336x280 .brand-name { top: 6px; font-size: 21px; line-height: 26px; }
  .banner--336x280 .headline { top: 39px; font-size: 14.5px; line-height: 17px; }
  .banner--336x280 .divider { top: 79px; }
  .banner--336x280 .cta { top: 87px; }
  .banner--336x280 .roof { height: 156px; }

  .banner--300x250 .brand-name { top: 6px; font-size: 18px; line-height: 24px; }
  .banner--300x250 .headline { top: 35px; font-size: 14.5px; line-height: 17px; }
  .banner--300x250 .divider { top: 75px; }
  .banner--300x250 .cta { top: 84px; }
  .banner--300x250 .roof { height: 127px; }

  .banner--300x600 .brand-name { top: 20px; font-size: 36px; line-height: 46px; }
  .banner--300x600 .headline { top: 84px; font-size: 16.5px; line-height: 21px; }
  .banner--300x600 .divider { top: 135px; }
  .banner--300x600 .cta { top: 151px; }
  .banner--300x600 .roof { height: 407px; }
</style>
</head>
<body>
<main class="stage">
  <div class="size-label" style="left:238px; top:55px;">336*280</div>
  <div class="size-label" style="left:607px; top:55px;">300*600</div>
  <div class="size-label" style="left:238px; top:407px;">300*250</div>

  <section class="banner banner--336x280" aria-label="Banner 336 by 280">
    <div class="brand-name">halvern</div>
    <h2 class="headline"><span>FAST BRIDGING LOANS</span><span>FROM 0.39% PM</span></h2>
    <div class="divider"></div>
    <a class="cta" href="#">GET STARTED</a>
    <svg class="roof" viewBox="0 0 336 156" preserveAspectRatio="none">
      <defs>
        <linearGradient id="meetingTones" x1="0" y1="0" x2="1" y2="1">
          <stop offset="0" stop-color="var(--photo-blue-dark)"/>
          <stop offset="0.5" stop-color="var(--photo-blue-light)"/>
          <stop offset="1" stop-color="var(--photo-blue-dark)"/>
        </linearGradient>
      </defs>
      <polygon points="0,44 168,0 336,44 336,156 0,156" fill="var(--white)"/>
      <polygon role="img" aria-label="Photo of a business team meeting in front of a chart screen" points="0,52 168,7 336,52 336,156 0,156" fill="url(#meetingTones)"/>
    </svg>
  </section>

  <section class="banner banner--300x250" aria-label="Banner 300 by 250">
    <div class="brand-name">halvern</div>
    <h2 class="headline"><span>FAST BRIDGING LOANS</span><span>FROM 0.39% PM</span></h2>
    <div class="divider"></div>
    <a class="cta" href="#">GET STARTED</a>
    <svg class="roof" viewBox="0 0 300 127" preserveAspectRatio="none">
      <defs>
        <linearGradient id="officeTones" x1="0" y1="0" x2="1" y2="1">
          <stop offset="0" stop-color="var(--photo-warm-light)"/>
          <stop offset="0.55" stop-color="var(--photo-warm-dark)"/>
          <stop offset="1" stop-color="var(--photo-warm-light)"/>
        </linearGradient>
      </defs>
      <polygon points="0,45 150,0 300,45 300,127 0,127" fill="var(--white)"/>
      <polygon role="img" aria-label="Photo of colleagues working together on laptops in an office" points="0,53 150,8 300,53 300,127 0,127" fill="url(#officeTones)"/>
    </svg>
  </section>

  <section class="banner banner--300x600" aria-label="Banner 300 by 600">
    <div class="brand-name">halvern</div>
    <h2 class="headline"><span>FAST BRIDGING LOANS</span><span>FROM 0.39% PM</span></h2>
    <div class="divider"></div>
    <a class="cta" href="#">GET STARTED</a>
    <svg class="roof" viewBox="0 0 300 407" preserveAspectRatio="none">
      <defs>
        <linearGradient id="deskTones" x1="0" y1="0" x2="1" y2="1">
          <stop offset="0" stop-color="var(--photo-slate-dark)"/>
          <stop offset="0.5" stop-color="var(--photo-slate-light)"/>
          <stop offset="1" stop-color="var(--photo-slate-dark)"/>
        </linearGradient>
      </defs>
      <polygon points="0,50 150,0 300,50 300,407 0,407" fill="var(--white)"/>
      <polygon role="img" aria-label="Photo of a businessman in glasses working at a laptop" points="0,54 150,7 300,54 300,407 0,407" fill="url(#deskTones)"/>
    </svg>
  </section>
</main>
</body>
</html>
```